Business Cards for IT Consulting Company (Managed Service Provider)

I am looking to have some business cards printed and would like some designs. We are an IT Consulting company based in Vancouver BC. I would like a nice clean and modern look to the cards. I have uploaded all the versions of my logo so parts can be used as needed. Here is a snippit from our website homepage:

Quillbrook Networks Ltd. is an IT Solutions Partner located in Vancouver BC, Canada. We offer IT solutions and support to customers in the greater Vancouver Area. With expertise in Microsoft platforms, as well as Linux and Mac OSX and over 12 years experience in the IT industry, Quillbrook Networks is dedicated to offering our clients top quality service and products. We take pride in the solutions we offer our customers. The greatest compliment a client can give us is to recommend our services.

Quillbrook Networks Ltd. offers a wide range of IT services from onsite service to remote support and managed service solutions. This allows clients to choose the support path that best suits their company’s needs. Supporting many different sized companies from small to enterprise level over the past 12 years Quillbrook Networks has the experience and expertise needed to ensure things run smoothly. Allowing our clients to focus on doing business.

Revolutionizing the way IT services are delivered.

Quillbrook Networks is dedicated to providing our clients with IT solutions that work and grow with them for years to come. This philosophy helps save money in the long run instead of replacing equipment constantly. Far too often IT solutions are not well thought out and while possibly solving the problem at hand, require replacement due to growth or quality within a very short time frame. Quillbrook Networks takes pride in providing solutions that will last and be able to accommodate growth without the need for replacement.

Industry/Entity Type

Information Technology

Contact Information for Business Card

Quillbrook Networks Ltd.
(Employee Name)
Eml: (Employees Email Address)
Web: quillbrook.me
Ph: 604-555-0148

Font styles to use
Serif
Sans Serif

Requirements
Must have
• The Company logo and company colors.
Nice to have
• - Our tag line: "Revolutionizing IT Services" or "Revolutionizing the way IT services are delivered."
• - Also I really like the idea of nature and technology together blending which is sort of where my logo came from so integrating that somehow onto the business cards would be great.

```html
<!DOCTYPE html>
<html lang="en">
<head>
<meta charset="utf-8">
<title>Quillbrook Networks Ltd. — Business Card</title>
<link href="https://fonts.googleapis.com/css2?family=Roboto:ital,wght@0,400;0,500;1,400&display=swap" rel="stylesheet">
<style>
  :root {
    --backdrop: #a8a6a7;
    --card: #f3f3f3;
    --brand-blue: #1e8fd6;
    --ink: #3f3f42;
    --ink-soft: #4a4a4d;
    --divider: #d6d6d6;
  }
  * { margin: 0; padding: 0; box-sizing: border-box; }
  html, body {
    width: 1200px; height: 1200px; overflow: hidden;
    background: var(--backdrop);
    font-family: "Roboto", Arial, sans-serif;
  }
  .canvas { position: relative; width: 1200px; height: 1200px; }
  .card {
    position: absolute; width: 712px; height: 418px;
    background: var(--card);
  }
  .card--front { left: 238px; top: 118px; }
  .card--back  { left: 230px; top: 644px; }

  /* Front */
  .brand {
    position: absolute; left: 109px; top: 126px;
    display: flex; align-items: center; gap: 26px;
    color: var(--brand-blue); font-weight: 500;
  }
  .brand__square { width: 84px; height: 84px; background: var(--brand-blue); flex: none; }
  .brand__name { font-size: 70px; line-height: 1; letter-spacing: -1px; }
  .brand__sub { font-size: 25px; letter-spacing: 0.5px; margin-top: 4px; }

  .tagline {
    position: absolute; left: 0; right: 0; top: 376px;
    display: flex; align-items: center; justify-content: center; gap: 16px;
    font-size: 18px; color: var(--ink-soft); letter-spacing: 0.3px;
  }
  .tagline__rule { width: 110px; height: 3px; background: var(--brand-blue); }

  /* Back */
  .back-brand {
    position: absolute; left: 88px; top: 190px;
    color: var(--brand-blue); font-weight: 500; font-size: 34px;
  }
  .back-divider {
    position: absolute; left: 341px; top: 84px; width: 1px; height: 248px;
    background: var(--divider);
  }
  .person { position: absolute; left: 400px; top: 128px; }
  .person__name { color: var(--brand-blue); font-weight: 500; font-size: 25px; }
  .person__role { color: var(--ink); font-style: italic; font-size: 16px; margin-top: 4px; }
  .contacts { list-style: none; margin-top: 26px; }
  .contacts li {
    display: flex; align-items: center; gap: 16px;
    font-size: 17.5px; color: var(--ink); height: 27px;
  }
  .contacts svg { width: 18px; height: 18px; fill: var(--brand-blue); flex: none; margin-left: 0; }
</style>
</head>
<body>
<div class="canvas">

  <section class="card card--front">
    <div class="brand">
      <span class="brand__square"></span>
      <div>
        <div class="brand__name">quillbrook</div>
        <div class="brand__sub">NETWORKS LTD.</div>
      </div>
    </div>
    <div class="tagline">
      <span class="tagline__rule"></span>
      <span>Revolutionizing IT Services</span>
      <span class="tagline__rule"></span>
    </div>
  </section>

  <section class="card card--back">
    <div class="back-brand">quillbrook</div>
    <div class="back-divider"></div>
    <div class="person">
      <div class="person__name">Daniel Reyes</div>
      <div class="person__role">Managing Director</div>
      <ul class="contacts">
        <li>
          <svg viewBox="0 0 20 20" aria-hidden="true"><path d="M4 3h3l2 4-2 1.5a10 10 0 0 0 4.5 4.5L13 11l4 2v3a2 2 0 0 1-2 2A14 14 0 0 1 2 5a2 2 0 0 1 2-2z"/></svg>
          <span>604-555-0148</span>
        </li>
        <li>
          <svg viewBox="0 0 20 20" aria-hidden="true"><path d="M10 1a9 9 0 1 0 0 18A9 9 0 0 0 10 1zm6.9 8h-3a14 14 0 0 0-1.3-5.6A7 7 0 0 1 16.9 9zM10 3c.9 1.2 1.7 3.4 1.9 6H8.1C8.3 6.4 9.1 4.2 10 3zM7.4 3.4A14 14 0 0 0 6.1 9h-3a7 7 0 0 1 4.3-5.6zM3.1 11h3a14 14 0 0 0 1.3 5.6A7 7 0 0 1 3.1 11zM10 17c-.9-1.2-1.7-3.4-1.9-6h3.8c-.2 2.6-1 4.8-1.9 6zm2.6-.4a14 14 0 0 0 1.3-5.6h3a7 7 0 0 1-4.3 5.6z"/></svg>
          <span>www.quillbrook.me</span>
        </li>
        <li>
          <svg viewBox="0 0 20 20" aria-hidden="true"><path d="M2 4h16v12H2zm1.5 1.5v.4L10 11l6.5-5.1v-.4zm0 2.3v6.7h13V7.8L10 13z"/></svg>
          <span>support@quillbrook.me</span>
        </li>
      </ul>
    </div>
  </section>

</div>
</body>
</html>
```